Car Signage & Personal Branding - Email & Letterhead

I require a ¼ wrap on 2014 Korvana Delmire Ridgeback - Colour Glacier Blue.
Covering the follow...
- rear panel and small window
- passenger door & ½ of the passenger window - top left to bottom right, can blend into drivers door. (more than what is showed on the image)

This design will then be required as Email & letter header and branding for advertising.

I'm a Gold Coast real estate agent and want something thats clear, professional, people say WOW and isn't like all other boring vehicle wraps.

To feature my image and get across that I'm honest reliable, ethical, tenacious, hard working, talented.

I do like these font advertising styles (see Word Doc) )but I'm not the professional and want something from you.

I like light sky/ocean blue but may not work against a light blue car. I like the way 2 photos are blended together, wonder if that can be done professionally with the gold coast & my photo.

Brindle colours are 100% black, cyan & white. Must have their logo on it.

Have included some font advertising styles that you may think would look good, obviously only use these if you think they're suitable.
Updates

Residential, development & land sales on the gold coast Added Thursday, June 11, 2015

Design can go over small rear window and the black plastic on the passenger window but not the glass. There must be a gap for the passenger door handle. The rear of the car, it can go over the glass & it must have all my phone number. Added Friday, June 12, 2015

Target Market(s)

Clients and other drivers

Industry/Entity Type

Real Estate Agent

Requirements
Must have
• My photo
• Company logo
• 040 555 3186
• lucyt@brindleco.com.au
• www.lucytambor.com
• Wave image
• Will cover the complete rear hatch of the car.
• can cover back rear ¼ glass window and then come down through passenger window on the angle to the bottom corner
Nice to have
• Image of Gold Coast or waves
• What you would imagine on a multi-million dollar real estate agents car
Should not have
• Can not cover drivers window
• Can not cover any door handles

```html
<!DOCTYPE html>
<html lang="en">
<head>
<meta charset="utf-8">
<title>Brindle – Letterhead</title>
<link rel="stylesheet" href="https://fonts.googleapis.com/css2?family=Open+Sans:wght@600;700&display=swap">
<style>
  :root {
    --cyan: #0fa8e0;
    --ink: #231f20;
    --paper: #ffffff;
    --rule: #d9dadb;
    --text: #231f20;
  }
  * { margin: 0; padding: 0; box-sizing: border-box; }
  html, body { width: 926px; height: 1200px; overflow: hidden; background: var(--paper); }
  body { font-family: "Open Sans", Arial, sans-serif; }

  .letterhead { position: relative; width: 926px; height: 1200px; background: var(--paper); }

  .top-stripe { position: absolute; left: 0; top: 0; width: 926px; height: 11px; background: var(--cyan); }

  .header-band {
    position: absolute; left: 0; top: 24px; width: 708px; height: 136px;
    background: var(--ink);
  }

  .brand {
    position: absolute; left: 36px; top: 56px;
    display: flex; align-items: center; gap: 14px;
  }
  .brand-dot { width: 58px; height: 58px; border-radius: 50%; background: var(--cyan); }
  .brand-name {
    color: var(--paper); font-weight: 700; font-size: 60px; line-height: 1;
    letter-spacing: -1px;
  }

  .agent-photo {
    position: absolute; left: 500px; top: 22px; width: 208px; height: 138px;
    background: linear-gradient(90deg, rgba(35,31,32,0) 0%, #8a7a63 35%, #d8c6a4 65%, #eef0f0 100%);
    border-top-left-radius: 120px 138px;
  }

  .contact {
    position: absolute; left: 696px; top: 68px; list-style: none;
  }
  .contact li {
    display: flex; align-items: center; gap: 6px;
    font-size: 14.5px; font-weight: 700; color: var(--text);
    height: 19px;
  }
  .contact svg { width: 13px; height: 13px; flex: none; }

  .contact-rule {
    position: absolute; left: 698px; top: 127px; width: 228px; height: 1px; background: var(--rule);
  }
</style>
</head>
<body>
<div class="letterhead">
  <div class="top-stripe"></div>
  <div class="header-band"></div>

  <div class="brand">
    <span class="brand-dot"></span>
    <span class="brand-name">Brindle</span>
  </div>

  <div class="agent-photo" role="img" aria-label="Portrait photo of the agent, Lucy Tambor"></div>

  <ul class="contact">
    <li>
      <svg viewBox="0 0 14 14"><circle cx="7" cy="7" r="6.2" fill="none" stroke="#0fa8e0" stroke-width="1.2"/><path d="M4.6 3.8l1.3-.3.8 1.9-.8.6c.4.9 1 1.5 1.9 1.9l.6-.8 1.9.8-.3 1.3c-2.9.2-5.6-2.5-5.4-5.4z" fill="#0fa8e0"/></svg>
      040 555 3186
    </li>
    <li>
      <svg viewBox="0 0 14 14"><circle cx="7" cy="7" r="6.8" fill="#0fa8e0"/><rect x="3.6" y="4.6" width="6.8" height="4.8" fill="#fff"/><path d="M3.6 4.6L7 7.3l3.4-2.7" fill="none" stroke="#0fa8e0" stroke-width=".9"/></svg>
      lucyt@brindleco.com.au
    </li>
    <li>
      <svg viewBox="0 0 14 14" fill="none" stroke="#0fa8e0" stroke-width="1.1"><circle cx="7" cy="7" r="6"/><ellipse cx="7" cy="7" rx="2.6" ry="6"/><path d="M1 7h12M2 4h10M2 10h10"/></svg>
      www.lucytambor.com
    </li>
  </ul>
  <div class="contact-rule"></div>
</div>
</body>
</html>
```